wealth management firm, professional group, new model

we have a logo that works but we need a card, white background using our colors...clean look

our tag line if can be used in

The Bridge From Client to Owner

```html
<!DOCTYPE html>
<html lang="en">
<head>
<meta charset="utf-8">
<title>Arvel Wealth Partners – Business Card</title>
<link rel="stylesheet" href="https://fonts.googleapis.com/css2?family=Montserrat:wght@400;700&family=Open+Sans:wght@400;600&display=swap">
<style>
  :root {
    --page-bg: #e9eaec;
    --navy: #1c2a5c;
    --card-blue: #182f55;
    --card-blue-text: #3a5c94;
    --white: #ffffff;
    --ink: #1c2a5c;
  }
  * { box-sizing: border-box; margin: 0; padding: 0; }
  html, body { width: 1200px; height: 875px; overflow: hidden; }
  body {
    background: var(--page-bg);
    font-family: "Open Sans", sans-serif;
    color: var(--ink);
    display: flex;
    flex-direction: column;
    align-items: center;
    justify-content: center;
    gap: 48px;
  }
  .card {
    width: 620px;
    height: 354px;
    border-radius: 22px;
    position: relative;
    box-shadow: 0 6px 18px rgba(0,0,0,0.12);
  }

  .brand {
    display: flex;
    align-items: center;
    gap: 16px;
  }
  .brand-dot {
    flex: none;
    width: 12px;
    height: 12px;
    border-radius: 50%;
    background: currentColor;
  }
  .brand-name {
    font-family: "Montserrat", sans-serif;
    font-weight: 400;
    text-transform: uppercase;
  }

  /* Back */
  .card-back {
    background: var(--card-blue);
    display: flex;
    align-items: center;
    justify-content: center;
  }
  .card-back .brand {
    color: var(--card-blue-text);
  }
  .card-back .brand-name {
    font-size: 22px;
    letter-spacing: 0.2em;
    white-space: nowrap;
  }

  /* Front */
  .card-front {
    background: var(--white);
    display: grid;
    grid-template-columns: 330px 1px 1fr;
    align-items: center;
  }
  .card-front .brand {
    justify-self: center;
    color: var(--navy);
    margin-top: 60px;
  }
  .card-front .brand-name {
    font-size: 15px;
    letter-spacing: 0.16em;
    line-height: 1.5;
    width: 220px;
  }
  .divider {
    width: 1px;
    height: 210px;
    background: var(--navy);
  }
  .contact {
    padding-left: 34px;
  }
  .person-name {
    font-family: "Montserrat", sans-serif;
    font-weight: 700;
    font-size: 24px;
    color: var(--navy);
    text-transform: uppercase;
    line-height: 1.1;
  }
  .person-role {
    font-size: 13px;
    margin-top: 2px;
  }
  .dash {
    width: 14px;
    height: 1px;
    background: var(--navy);
    margin: 20px 0 22px 10px;
  }
  .address {
    font-size: 13px;
    line-height: 1.35;
    margin-left: 10px;
    margin-bottom: 10px;
  }
  .contact-list {
    list-style: none;
    font-size: 13px;
    line-height: 1.45;
    margin-left: 10px;
  }
  .contact-list li {
    display: flex;
    align-items: center;
    gap: 7px;
  }
  .contact-list svg {
    width: 10px;
    height: 10px;
    fill: var(--navy);
    flex: none;
  }
</style>
</head>
<body>

  <section class="card card-back" aria-label="Card back">
    <div class="brand">
      <span class="brand-dot"></span>
      <span class="brand-name">Arvel Wealth Partners</span>
    </div>
  </section>

  <section class="card card-front" aria-label="Card front">
    <div class="brand">
      <span class="brand-dot"></span>
      <span class="brand-name">Arvel Wealth Partners</span>
    </div>
    <div class="divider"></div>
    <div class="contact">
      <h1 class="person-name">Dana Reyes</h1>
      <p class="person-role">Manager</p>
      <div class="dash"></div>
      <p class="address">Your loaction street here,<br>Your country name - 9120</p>
      <ul class="contact-list">
        <li>
          <svg viewBox="0 0 10 10" aria-hidden="true"><path d="M2 0.5 L3.6 2.6 L2.8 3.6 C3.4 5 4.9 6.5 6.4 7.2 L7.4 6.4 L9.5 8 L8.4 9.5 C4.5 9.2 0.8 5.5 0.5 1.6 Z"/></svg>
          +012 345 6789
        </li>
        <li>
          <svg viewBox="0 0 10 10" aria-hidden="true"><path d="M0.5 2 H9.5 V8.5 H0.5 Z M1.2 2.6 L5 5.6 L8.8 2.6" stroke="#fff" stroke-width="0.8"/></svg>
          info@youremail.com
        </li>
        <li>
          <svg viewBox="0 0 10 10" aria-hidden="true"><circle cx="5" cy="5" r="4.5"/><path d="M0.8 5 H9.2 M5 0.6 C3 3 3 7 5 9.4 M5 0.6 C7 3 7 7 5 9.4" stroke="#fff" stroke-width="0.7" fill="none"/></svg>
          www.yourwebsite.com
        </li>
      </ul>
    </div>
  </section>

</body>
</html>
```